Business card for a Exhibition booth fabrication company

Hi. My company would like to change our corporate name card. We are an events and Exhibition stand builder company. We would like our corporate name card to resonate what we do. I need someone to create something unique that relates to the industry that I am in. The graphic designer should be creative to incorporate the elements of my industry and try to blend in well in the design of the card. Our aim is to ensure that we are unique and our card can look different from our competitors.
Updates

Target Market(s)

Marketing and events manager from all companies

Contact Information for Business Card

The business card should have the following details:
Name
Job Title
Email
Website

Colors

Designer to choose colors to be used in the design.

Requirements
Must have
• The card must be look something that is relevant to the service that I am providing. My website is: www.velmora-buildworks.com
• You can see my website to get more information on what service that I am doing
Nice to have
• On the back of my card, I would like to have a globe image with the incorporation of my company logo. This is to indicate that my services can be done in any part of the world.

```html
<!DOCTYPE html>
<html lang="en">
<head>
<meta charset="utf-8">
<title>Velmora Buildworks – Business Card</title>
<link rel="stylesheet" href="https://fonts.googleapis.com/css2?family=Arimo:wght@400;700&family=Open+Sans:wght@400&display=swap">
<style>
  :root {
    --stage-light: #dcdddf;
    --stage-dark: #a3a4a7;
    --card-white: #ffffff;
    --card-edge: #5a5a5c;
    --brand-red: #ed1c24;
    --brand-red-soft: #f4a0a3;
    --ink-grey: #5d5e60;
    --back-grey: #636466;
    --map-grey: #7b7c7e;
    --silver: #c9cacc;
    --url-white: #f2f2f2;
  }
  * { margin: 0; padding: 0; box-sizing: border-box; }
  html, body { width: 1200px; height: 1118px; overflow: hidden; }
  body {
    background: linear-gradient(90deg, var(--stage-light) 0%, #c3c4c6 55%, var(--stage-dark) 100%);
    position: relative;
  }
  .card {
    position: absolute;
    left: 222px;
    width: 756px;
    height: 432px;
    border-radius: 22px;
    overflow: hidden;
  }
  .card--front {
    top: 92px;
    background: var(--card-white);
    border: 1px solid var(--card-edge);
  }
  .card--back {
    top: 583px;
    background: var(--back-grey);
  }

  /* Front */
  .brand {
    position: absolute;
    left: 40px;
    top: 78px;
    display: flex;
    align-items: center;
    gap: 12px;
  }
  .brand__square {
    width: 22px;
    height: 22px;
    background: var(--brand-red);
  }
  .brand__name {
    font-family: "Arimo", Arial, sans-serif;
    font-weight: 700;
    font-size: 27px;
    letter-spacing: 2.5px;
    color: var(--ink-grey);
  }
  .holder {
    position: absolute;
    right: 26px;
    top: 114px;
    text-align: right;
    font-family: "Arimo", Arial, sans-serif;
  }
  .holder__name {
    font-weight: 700;
    font-size: 25px;
    color: var(--brand-red);
    letter-spacing: 0.5px;
    line-height: 30px;
  }
  .holder__title {
    font-size: 19px;
    color: var(--ink-grey);
    letter-spacing: 0.8px;
    line-height: 28px;
  }
  .contacts {
    position: absolute;
    left: 38px;
    top: 232px;
    list-style: none;
    font-family: "Open Sans", Arial, sans-serif;
    font-size: 18px;
    color: var(--ink-grey);
  }
  .contacts__item {
    display: flex;
    align-items: center;
    gap: 12px;
    height: 34.5px;
  }
  .contacts__icon { width: 18px; height: 18px; flex: none; }
  .address-band {
    position: absolute;
    left: 0;
    top: 350px;
    width: 756px;
    height: 42px;
  }
  .address-band__shape { position: absolute; inset: 0; }
  .address-band__text {
    position: absolute;
    left: 38px;
    top: 0;
    line-height: 42px;
    font-family: "Open Sans", Arial, sans-serif;
    font-size: 17.5px;
    color: var(--card-white);
  }

  /* Back */
  .world-map {
    position: absolute;
    left: 0;
    top: 70px;
    width: 756px;
    height: 300px;
    background: radial-gradient(ellipse at 50% 45%, var(--map-grey) 0%, #717274 55%, rgba(99,100,102,0) 80%);
  }
  .back-brand {
    position: absolute;
    left: 0;
    right: 0;
    top: 200px;
    text-align: center;
    font-family: "Arimo", Arial, sans-serif;
    font-weight: 700;
    font-size: 46px;
    letter-spacing: 3px;
    color: var(--silver);
  }
  .back-url {
    position: absolute;
    left: 0;
    right: 0;
    top: 388px;
    text-align: center;
    font-family: "Open Sans", Arial, sans-serif;
    font-size: 21px;
    letter-spacing: 4.5px;
    color: var(--url-white);
  }
</style>
</head>
<body>

<section class="card card--front" aria-label="Business card front">
  <div class="brand">
    <span class="brand__square"></span>
    <span class="brand__name">VELMORA BUILDWORKS</span>
  </div>

  <div class="holder">
    <p class="holder__name">DANIEL HARWICK</p>
    <p class="holder__title">PRESIDENT</p>
  </div>

  <ul class="contacts">
    <li class="contacts__item">
      <svg class="contacts__icon" viewBox="0 0 24 24" aria-hidden="true">
        <path fill="#ed1c24" d="M6.6 10.8c1.4 2.8 3.8 5.1 6.6 6.6l2.2-2.2c.3-.3.7-.4 1-.2 1.1.4 2.3.6 3.6.6.6 0 1 .4 1 1V20c0 .6-.4 1-1 1C10.6 21 3 13.4 3 4c0-.6.4-1 1-1h3.5c.6 0 1 .4 1 1 0 1.3.2 2.5.6 3.6.1.3 0 .7-.2 1L6.6 10.8z"/>
      </svg>
      <span>012-345-6789</span>
    </li>
    <li class="contacts__item">
      <svg class="contacts__icon" viewBox="0 0 24 24" aria-hidden="true">
        <rect x="2" y="5" width="20" height="14" fill="#ed1c24"/>
        <path d="M2 5l10 8 10-8M2 19l7.5-7M22 19l-7.5-7" fill="none" stroke="#fff" stroke-width="1.6"/>
      </svg>
      <span>info@velmora-buildworks.com</span>
    </li>
    <li class="contacts__item">
      <svg class="contacts__icon" viewBox="0 0 24 24" aria-hidden="true">
        <g fill="none" stroke="#ed1c24" stroke-width="1.7">
          <circle cx="12" cy="12" r="9.5"/>
          <ellipse cx="12" cy="12" rx="4.2" ry="9.5"/>
          <path d="M2.5 12h19M4 7h16M4 17h16"/>
        </g>
      </svg>
      <span>www.velmora-buildworks.com</span>
    </li>
  </ul>

  <div class="address-band">
    <svg class="address-band__shape" viewBox="0 0 756 42" preserveAspectRatio="none" aria-hidden="true">
      <polygon points="0,0 588,0 562,42 0,42" fill="#ed1c24"/>
      <path d="M728,0 H756 V42 H728 Q740,21 728,0 Z" fill="#ed1c24"/>
      <circle cx="660" cy="21" r="17" fill="#f4a0a3"/>
    </svg>
    <span class="address-band__text">Street Name, City Name, Zipcode - 01234</span>
  </div>
</section>

<section class="card card--back" aria-label="Business card back">
  <div class="world-map" role="img" aria-label="Light grey world map spanning the card"></div>
  <p class="back-brand">VELMORA BUILDWORKS</p>
  <p class="back-url">www.velmora-buildworks.com</p>
</section>

</body>
</html>
```